A clean crisp business card for a Landscape Construction company. Designed to be easy to read contact/ info and also be appealing/interesting, unlike a traditional business card.

Industry/Entity Type

Landscape Construction

Contact Information for Business Card

Company name : Brambleford Landscape Construction, phone number: (877) 62Vista, website:Bramblefordyards.example, Email, sales@bramblefordyards.example

Requirements
Nice to have
• Luxurious finishes/ details…. Icons or emblems next to contact info
Should not have
• Clipart or general pictures

```html
<!DOCTYPE html>
<html lang="en">
<head>
<meta charset="utf-8">
<title>Brambleford Landscape Construction – Business Card</title>
<link rel="stylesheet" href="https://fonts.googleapis.com/css2?family=Cinzel:wght@400;700&family=Arimo:wght@400&display=swap">
<style>
  :root {
    --bg: #b9b9b9;
    --brand-blue: #206bb5;
    --leaf-green: #8cc63f;
    --ink: #2b2b2b;
    --paper: #ffffff;
  }
  * { margin: 0; padding: 0; box-sizing: border-box; }
  html, body { width: 1200px; height: 788px; overflow: hidden; }
  body {
    background: var(--bg);
    display: flex;
    align-items: center;
    justify-content: center;
    gap: 40px;
  }
  .card {
    position: relative;
    width: 540px;
    height: 309px;
    border-radius: 22px;
    overflow: hidden;
    box-shadow: 0 10px 24px rgba(0,0,0,0.25);
  }
  .card--front { background: var(--paper); }
  .card--back {
    background: var(--brand-blue);
    display: flex;
    flex-direction: column;
    align-items: center;
    justify-content: center;
  }
  .wave { position: absolute; inset: 0; width: 100%; height: 100%; }

  .brand-name {
    font-family: "Cinzel", serif;
    font-weight: 400;
    text-align: center;
    letter-spacing: 0.06em;
    line-height: 1.2;
  }
  .card--front .brand-name {
    position: absolute;
    left: 24px;
    top: 92px;
    width: 230px;
    color: var(--brand-blue);
    font-size: 24px;
  }
  .card--front .brand-name .brand-sub { font-size: 24px; display: block; }
  .card--back .brand-name {
    color: var(--paper);
    font-size: 40px;
  }

  .divider {
    position: absolute;
    left: 268px;
    top: 60px;
    width: 1px;
    height: 120px;
    background: var(--leaf-green);
  }

  .contact {
    position: absolute;
    left: 288px;
    top: 46px;
    font-family: "Arimo", sans-serif;
    color: var(--ink);
  }
  .person-name {
    font-family: "Cinzel", serif;
    font-weight: 700;
    font-size: 22px;
    letter-spacing: 0.02em;
    line-height: 1;
  }
  .person-name .first { color: var(--brand-blue); }
  .person-name .last { color: var(--leaf-green); }
  .person-title { font-size: 14px; margin: 4px 0 12px; }
  .contact-list { list-style: none; }
  .contact-item {
    display: flex;
    align-items: center;
    gap: 8px;
    font-size: 13px;
    line-height: 1;
    margin-bottom: 9px;
  }
  .contact-icon { width: 14px; height: 14px; flex: none; }
</style>
</head>
<body>

  <section class="card card--front" aria-label="Business card front">
    <svg class="wave" viewBox="0 0 540 309" preserveAspectRatio="none" aria-hidden="true">
      <path d="M0,292 C160,290 260,262 340,228 S470,192 540,186 L540,309 L0,309 Z" fill="var(--leaf-green)"/>
      <path d="M0,300 C165,298 268,272 348,238 S475,200 540,194 L540,309 L0,309 Z" fill="var(--paper)"/>
      <path d="M0,304 C168,302 272,278 352,244 S478,206 540,200 L540,309 L0,309 Z" fill="var(--brand-blue)"/>
    </svg>

    <div class="brand-name">Brambleford<span class="brand-sub">Landscape Construction</span></div>

    <div class="divider"></div>

    <div class="contact">
      <p class="person-name"><span class="first">Owen</span> <span class="last">Hartley</span></p>
      <p class="person-title">Founder</p>
      <ul class="contact-list">
        <li class="contact-item">
          <svg class="contact-icon" viewBox="0 0 16 16" aria-hidden="true">
            <path d="M3 2 L6 2 L7 5 L5.5 6.5 C6.5 8.5 7.5 9.5 9.5 10.5 L11 9 L14 10 L14 13 C14 13.6 13.6 14 13 14 C7 14 2 9 2 3 C2 2.4 2.4 2 3 2 Z" fill="var(--brand-blue)"/>
          </svg>
          (877) 62Vista
        </li>
        <li class="contact-item">
          <svg class="contact-icon" viewBox="0 0 16 16" aria-hidden="true">
            <rect x="1" y="3" width="14" height="10" rx="1" fill="var(--brand-blue)"/>
            <polyline points="1.5,3.5 8,9 14.5,3.5" fill="none" stroke="var(--paper)" stroke-width="1.2"/>
          </svg>
          sales@bramblefordyards.example
        </li>
        <li class="contact-item">
          <svg class="contact-icon" viewBox="0 0 16 16" aria-hidden="true">
            <circle cx="8" cy="8" r="7" fill="var(--brand-blue)"/>
            <ellipse cx="8" cy="8" rx="3" ry="7" fill="none" stroke="var(--paper)" stroke-width="1"/>
            <line x1="1" y1="8" x2="15" y2="8" stroke="var(--paper)" stroke-width="1"/>
          </svg>
          bramblefordyards.example
        </li>
      </ul>
    </div>
  </section>

  <section class="card card--back" aria-label="Business card back">
    <div class="brand-name">Brambleford<br>Landscape Construction</div>
  </section>

</body>
</html>
```